Sea Shipping Logistics Company

The business is a logistics company (sea shipping and other special logistics) and also sales of bulk building materials.
The Design should be minimalistic and give a feeling of power and connectivity.
When the client sees the card, they should get a feeling of confident. Dark overall color (background) and print should be red / white .See logo. The card will be printed on trifecta with the middle color being red.

One side should be the logo and a 5 / 6 word slogan
And other side name, contact (phone/email) and a QR Code.

Target Market(s)

Construction companies / Oil & Gas related companies

Industry/Entity Type

Sea Bulk Shipping Logistics

Contact Information for Business Card

Name, Telephone number, Email address, Website URL, QR Code (see description)

Font styles to use
Sans Serif

Requirements
Must have
• No idea
Nice to have
• Minimalistic, but strong and powerful look and feel.

```html
<!DOCTYPE html>
<html lang="en">
<head>
<meta charset="utf-8">
<title>TORRA Freight – Business Card</title>
<link rel="stylesheet" href="https://fonts.googleapis.com/css2?family=Archivo:wght@800;900&family=Poppins:wght@400&family=Roboto:wght@400&display=swap">
<style>
  :root {
    --page-bg: #252222;
    --card-bg: #1f1f20;
    --card-bg-light: #262627;
    --red: #d0021b;
    --white: #f2f2f2;
    --grey: #8a8a8a;
    --divider: #111111;
    --qr-fill: #e6e6e6;
  }
  * { margin: 0; padding: 0; box-sizing: border-box; }
  html, body { width: 1200px; height: 1200px; overflow: hidden; }
  body { background: var(--page-bg); position: relative; font-family: "Roboto", sans-serif; }

  .card {
    position: absolute;
    width: 594px;
    height: 350px;
    border-radius: 22px;
    background: linear-gradient(160deg, var(--card-bg-light), var(--card-bg));
    overflow: hidden;
  }
  .card-front { left: 300px; top: 198px; }
  .card-back { left: 300px; top: 637px; }

  .logo-square { border: 4px solid currentColor; flex: none; }
  .logo-name {
    font-family: "Archivo", sans-serif;
    font-weight: 900;
    line-height: 1;
    white-space: nowrap;
    color: currentColor;
  }

  /* Front */
  .front-logo {
    position: absolute;
    left: 0; right: 0; top: 104px; height: 115px;
    display: flex; justify-content: center; align-items: center; gap: 16px;
    color: var(--grey);
  }
  .front-logo .logo-square { width: 115px; height: 115px; }
  .front-logo .logo-name { font-size: 46px; letter-spacing: -0.5px; }
  .slogan {
    position: absolute; left: 0; right: 0; top: 294px;
    display: flex; justify-content: center; align-items: center; gap: 14px;
    font-family: "Poppins", sans-serif;
    font-size: 14.5px; letter-spacing: 1.4px;
    color: var(--white);
  }
  .slogan-sep { width: 1.5px; height: 15px; background: var(--red); }

  /* Back */
  .red-band { position: absolute; left: 0; top: 0; bottom: 0; width: 60px; background: var(--red); }
  .band-divider { position: absolute; left: 60px; top: 0; bottom: 0; width: 6px; background: var(--divider); }
  .back-logo {
    position: absolute; left: 90px; top: 28px; height: 82px;
    display: flex; align-items: center; gap: 12px;
    color: var(--white);
  }
  .back-logo .logo-square { width: 92px; height: 82px; border-width: 3px; }
  .back-logo .logo-name { font-size: 46px; letter-spacing: -0.5px; }
  .qr-code {
    position: absolute; right: 30px; top: 28px;
    width: 84px; height: 84px;
    background: var(--qr-fill);
    border-radius: 4px;
  }
  .person { position: absolute; left: 90px; top: 202px; }
  .person-name {
    font-family: "Archivo", sans-serif; font-weight: 800;
    font-size: 25px; color: var(--red); letter-spacing: 0.5px; line-height: 1.1;
  }
  .person-title { font-size: 16px; color: var(--white); margin-top: 4px; }
  .contact-list { position: absolute; top: 272px; list-style: none; }
  .contact-left { left: 90px; }
  .contact-right { left: 385px; top: 270px; }
  .contact-item {
    display: flex; align-items: center; gap: 10px;
    font-size: 16px; color: var(--white); height: 23px; white-space: nowrap;
  }
  .contact-item svg { width: 14px; height: 14px; flex: none; fill: var(--red); }
</style>
</head>
<body>
  <section class="card card-front">
    <div class="front-logo">
      <div class="logo-square"></div>
      <div class="logo-name">TORRA FREIGHT</div>
    </div>
    <div class="slogan">
      <span>SHIPPING</span><span class="slogan-sep"></span>
      <span>LOGISTICS</span><span class="slogan-sep"></span>
      <span>MATERIALS</span>
    </div>
  </section>

  <section class="card card-back">
    <div class="red-band"></div>
    <div class="band-divider"></div>
    <div class="back-logo">
      <div class="logo-square"></div>
      <div class="logo-name">TORRA</div>
    </div>
    <div class="qr-code" role="img" aria-label="QR code linking to the company website"></div>
    <div class="person">
      <div class="person-name">MARK ELLISON</div>
      <div class="person-title">Managing Director</div>
    </div>
    <ul class="contact-list contact-left">
      <li class="contact-item">
        <svg viewBox="0 0 16 16"><path d="M1 6c0-2 3-3 7-3s7 1 7 3v1h-3V5.5C11 5 9.5 5 8 5s-3 0-4 .5V7H1zM4 8h8l2 6H2z"/></svg>
        +597 555-0142
      </li>
      <li class="contact-item">
        <svg viewBox="0 0 16 16"><path d="M8 0a5.5 5.5 0 0 0-5.5 5.5C2.5 10 8 16 8 16s5.5-6 5.5-10.5A5.5 5.5 0 0 0 8 0zm0 8a2.5 2.5 0 1 1 0-5 2.5 2.5 0 0 1 0 5z"/></svg>
        Havenweg 12, Suriname
      </li>
    </ul>
    <ul class="contact-list contact-right">
      <li class="contact-item">
        <svg viewBox="0 0 16 16"><path d="M0 3h16v10H0zm1.5 1.5v.4L8 9l6.5-4.1v-.4z"/></svg>
        info@torra-freight.com
      </li>
      <li class="contact-item">
        <svg viewBox="0 0 16 16"><path d="M8 0a8 8 0 1 0 0 16A8 8 0 0 0 8 0zm5.9 7.2h-2.6a12 12 0 0 0-1-4.9 6.4 6.4 0 0 1 3.6 4.9zM8 1.7c.8 1 1.6 3 1.7 5.5H6.3C6.4 4.7 7.2 2.7 8 1.7zM5.7 2.3a12 12 0 0 0-1 4.9H2.1a6.4 6.4 0 0 1 3.6-4.9zM2.1 8.8h2.6a12 12 0 0 0 1 4.9 6.4 6.4 0 0 1-3.6-4.9zM8 14.3c-.8-1-1.6-3-1.7-5.5h3.4c-.1 2.5-.9 4.5-1.7 5.5zm2.3-.6a12 12 0 0 0 1-4.9h2.6a6.4 6.4 0 0 1-3.6 4.9z"/></svg>
        www.torra-freight.com
      </li>
    </ul>
  </section>
</body>
</html>
```